Marlowe Ledger needs a postcard for Tax Resolutions Services

Marlowe Ledger specializes in helping taxpayers solve their problems with the QTB or state tax agencies. Whether it's back taxes, errors by other tax preparers or non paid employer taxes. We handle everything including but not limited to tax return amendments, penalty abatements, installment agreements, Injured/Innocent Spouse, Audits, Offers In Compromise, Tax Liens, and Tax Levys.

Primarily this postcard will be sent to taxpayers who have had a tax lien filed against them recently (in the past 30-90 days). We don't do hard sales, but want to urge prospects that there are ways to either lower their tax debt or get into manageable payments so that it's not so over whelming for them. Our ultimate goal is to help the taxpayers navigate this process and make it as painless for them as possible.

Target Market(s)

Typically small businesses owners and self-employed independent contractors ages 35-55 (who owe back taxes)

Industry/Entity Type

Accountant

Font styles to use
Serif
Sans Serif

Colors

Designer to choose colors to be used in the design.

Requirements
Must have
• Company logo, call to action with phone number,
• Please submit in flat format, with one side on top of the other. So that both sides can be easily seen and red. 3D views not necessary.
• Use colors from logo - Gold #C6A734, Purple: 5F1547
Nice to have
• Notification that prospects can schedule consultations online
Should not have
• No cartoony feel.
• Photos from my website

```html
<!DOCTYPE html>
<html lang="en">
<head>
<meta charset="utf-8">
<title>Marlowe Ledger – Tax Resolution Postcard</title>
<link href="https://fonts.googleapis.com/css2?family=Kreon:wght@600&family=Montserrat:wght@500;600&family=Raleway:wght@400;500&display=swap" rel="stylesheet">
<style>
  :root {
    --gold: #c6a734;
    --purple: #5f1547;
    --mauve-dark: #8c6583;
    --mauve-light: #d8c2d2;
    --ink: #2f2a2d;
    --muted: #4d474b;
    --rule: #bdbdbd;
    --badge-bg: #eeeeee;
    --page: #e7e4e3;
    --white: #ffffff;
  }
  * { box-sizing: border-box; margin: 0; padding: 0; }
  html, body { width: 913px; height: 1200px; overflow: hidden; }
  body { background: var(--page); position: relative; font-family: "Raleway", sans-serif; color: var(--ink); }

  .postcard { position: absolute; left: 93px; width: 701px; height: 451px; background: var(--white); box-shadow: 0 3px 10px rgba(0,0,0,.18); overflow: hidden; }
  .postcard--front { top: 103px; }
  .postcard--back { top: 650px; }

  /* front */
  .hero-photo { position: absolute; left: 0; top: 0; width: 701px; height: 334px;
    background: linear-gradient(160deg, var(--mauve-light) 0%, #b996ad 45%, var(--mauve-dark) 100%); }
  .headline { position: absolute; left: 26px; font-family: "Kreon", serif; font-weight: 600; font-size: 37px; color: var(--white); line-height: 1; padding-left: 14px; display: flex; align-items: center; }
  .headline--gold { top: 36px; width: 363px; height: 64px; background: var(--gold); }
  .headline--purple { top: 109px; width: 266px; height: 58px; background: var(--purple); }
  .accent-bar { position: absolute; top: 334px; height: 13px; }
  .accent-bar--gold { left: 0; width: 351px; background: var(--gold); }
  .accent-bar--purple { left: 351px; width: 350px; background: var(--purple); }

  .brand { position: absolute; display: flex; align-items: center; gap: 8px; font-family: "Montserrat", sans-serif; font-weight: 600; font-size: 19px; color: var(--gold); letter-spacing: .3px; }
  .brand__mark { width: 24px; height: 24px; background: var(--gold); border-radius: 50%; }
  .postcard--front .brand { left: 26px; top: 384px; }

  .front-copy { position: absolute; left: 253px; top: 362px; width: 423px; }
  .front-copy h2 { font-family: "Montserrat", sans-serif; font-weight: 600; font-size: 15px; color: var(--gold); margin-bottom: 5px; }
  .front-copy p { font-size: 9.8px; line-height: 1.3; text-align: justify; color: var(--ink); }
  .front-copy p + p { margin-top: 6px; }
  .phone { color: var(--gold); }

  /* back */
  .services-title { position: absolute; left: 27px; top: 26px; font-family: "Montserrat", sans-serif; font-weight: 600; font-size: 16px; line-height: 1.35; color: var(--gold); }
  .service-list { position: absolute; top: 78px; list-style: none; font-size: 11px; color: var(--muted); }
  .service-list li { height: 17px; display: flex; align-items: center; gap: 6px; }
  .service-list svg { width: 8px; height: 8px; flex: none; }
  .service-list--left { left: 32px; }
  .service-list--right { left: 192px; }
  .services-note { position: absolute; left: 27px; top: 154px; width: 310px; font-size: 10.5px; line-height: 1.33; color: var(--muted); }
  .services-note .cta { color: var(--gold); }

  .memberships { position: absolute; left: 18px; top: 202px; width: 325px; height: 65px; background: var(--badge-bg); display: flex; align-items: center; gap: 26px; padding-left: 17px; }
  .membership-badge { height: 32px; background: #c9c3cc; border-radius: 2px; }
  .membership-badge--society { width: 128px; }
  .membership-badge--association { width: 144px; }

  .agent-card { position: absolute; left: 18px; top: 298px; width: 325px; height: 127px; background: var(--purple); color: var(--white); }
  .agent-photo { position: absolute; left: 31px; top: 282px; width: 110px; height: 134px; border: 3px solid var(--white); background: linear-gradient(180deg, #3a3a3a, #151515); }
  .agent-name { position: absolute; left: 141px; top: 13px; font-family: "Raleway", sans-serif; font-weight: 500; font-size: 19px; }
  .agent-details { position: absolute; left: 141px; top: 49px; list-style: none; font-size: 9.8px; line-height: 1.35; }
  .agent-details li { display: flex; gap: 5px; margin-bottom: 5px; }
  .agent-details svg { width: 8px; height: 8px; flex: none; margin-top: 2px; }

  .stamp-box { position: absolute; left: 596px; top: 23px; width: 73px; height: 71px; border: 1px solid var(--rule); }
  .address-line { position: absolute; left: 441px; width: 228px; height: 1px; background: var(--rule); }

  .postcard--back .brand { left: 453px; top: 340px; }
  .web-note { position: absolute; left: 408px; width: 260px; text-align: center; color: var(--muted); }
  .web-note--lead { top: 388px; font-size: 10.5px; }
  .web-note--url { top: 404px; font-size: 13.5px; letter-spacing: .5px; }
</style>
</head>
<body>

<section class="postcard postcard--front">
  <div class="hero-photo" role="img" aria-label="Stressed man at a desk with laptop, calculator and glasses, tinted purple"></div>
  <h1 class="headline headline--gold">Financial Freedom</h1>
  <div class="headline headline--purple">From The QTB</div>
  <div class="accent-bar accent-bar--gold"></div>
  <div class="accent-bar accent-bar--purple"></div>

  <div class="brand"><span class="brand__mark"></span>MARLOWE LEDGER</div>

  <div class="front-copy">
    <h2>Are you having problems with the QTB?</h2>
    <p>Marlowe Ledger in Fairmont is here to help you resolve your tax problems and put an end to the misery that the QTB can put you through. We pride ourselves on being very efficient, affordable, and, of course, extremely discrete.</p>
    <p>Please call our office at <span class="phone">(555) 014-2290</span> to set up a free consultation.</p>
  </div>
</section>

<section class="postcard postcard--back">
  <h2 class="services-title">We can help you with the following<br>QTB tax problems:</h2>

  <ul class="service-list service-list--left">
    <li><svg viewBox="0 0 10 10"><rect x="0.5" y="0.5" width="9" height="9" fill="none" stroke="#c6a734"/><path d="M2.5 5l2 2 3.5-4" fill="none" stroke="#c6a734" stroke-width="1.3"/></svg>Wage Garnishment</li>
    <li><svg viewBox="0 0 10 10"><rect x="0.5" y="0.5" width="9" height="9" fill="none" stroke="#c6a734"/><path d="M2.5 5l2 2 3.5-4" fill="none" stroke="#c6a734" stroke-width="1.3"/></svg>Bank Levy</li>
    <li><svg viewBox="0 0 10 10"><rect x="0.5" y="0.5" width="9" height="9" fill="none" stroke="#c6a734"/><path d="M2.5 5l2 2 3.5-4" fill="none" stroke="#c6a734" stroke-width="1.3"/></svg>Threatening Letters</li>
    <li><svg viewBox="0 0 10 10"><rect x="0.5" y="0.5" width="9" height="9" fill="none" stroke="#c6a734"/><path d="M2.5 5l2 2 3.5-4" fill="none" stroke="#c6a734" stroke-width="1.3"/></svg>QTB Audit Notification</li>
  </ul>
  <ul class="service-list service-list--right">
    <li><svg viewBox="0 0 10 10"><rect x="0.5" y="0.5" width="9" height="9" fill="none" stroke="#c6a734"/><path d="M2.5 5l2 2 3.5-4" fill="none" stroke="#c6a734" stroke-width="1.3"/></svg>Non-Filing</li>
    <li><svg viewBox="0 0 10 10"><rect x="0.5" y="0.5" width="9" height="9" fill="none" stroke="#c6a734"/><path d="M2.5 5l2 2 3.5-4" fill="none" stroke="#c6a734" stroke-width="1.3"/></svg>Liens</li>
    <li><svg viewBox="0 0 10 10"><rect x="0.5" y="0.5" width="9" height="9" fill="none" stroke="#c6a734"/><path d="M2.5 5l2 2 3.5-4" fill="none" stroke="#c6a734" stroke-width="1.3"/></svg>Offers-in-Compromise</li>
    <li><svg viewBox="0 0 10 10"><rect x="0.5" y="0.5" width="9" height="9" fill="none" stroke="#c6a734"/><path d="M2.5 5l2 2 3.5-4" fill="none" stroke="#c6a734" stroke-width="1.3"/></svg>Innocent Spouse</li>
  </ul>

  <p class="services-note">Resolve your QTB tax problem with the peace of mind that you are in good hands, <span class="cta">please call us at (555) 014-2290</span> or contact us to set up a free consultation.</p>

  <div class="memberships">
    <div class="membership-badge membership-badge--society"></div>
    <div class="membership-badge membership-badge--association"></div>
  </div>

  <div class="agent-card">
    <div class="agent-name">Dana Whitfield EA</div>
    <ul class="agent-details">
      <li><svg viewBox="0 0 10 10"><rect width="10" height="10" fill="#fff"/><path d="M5 2a2 2 0 0 0-2 2c0 1.5 2 4 2 4s2-2.5 2-4a2 2 0 0 0-2-2z" fill="#5f1547"/></svg><span>1840 Harbor Mill Rd, 210, #114<br>Fairmont, GA 30999</span></li>
      <li><svg viewBox="0 0 10 10"><rect width="10" height="10" fill="#fff"/><path d="M3 2.5l1.3 1.5-.7.9a4 4 0 0 0 1.6 1.6l.9-.7L7.5 7 7 7.8C4.5 7.5 2.5 5.5 2.2 3z" fill="#5f1547"/></svg><span>(555) 014-4TAX</span></li>
      <li><svg viewBox="0 0 10 10"><rect width="10" height="10" fill="#fff"/><path d="M2 3h6v4H2z M2 3l3 2.2L8 3" fill="none" stroke="#5f1547" stroke-width=".9"/></svg><span>dana.whitfield@marloweledger.com</span></li>
    </ul>
  </div>
  <div class="agent-photo" role="img" aria-label="Portrait photo of the enrolled agent"></div>

  <div class="stamp-box"></div>
  <div class="address-line" style="top:175px"></div>
  <div class="address-line" style="top:208px"></div>
  <div class="address-line" style="top:240px"></div>
  <div class="address-line" style="top:272px"></div>

  <div class="brand"><span class="brand__mark"></span>MARLOWE LEDGER</div>
  <p class="web-note web-note--lead">For more information please visit our website</p>
  <p class="web-note web-note--url">www.marloweledger.com</p>
</section>

</body>
</html>
```